Brightway Haul & Upkeep Services, are a company that offers a 'one stop shop' pre-move clean up a

I have already selected a logo which I would like on the front of the business cards along with phone numbers, web address and email which are:
0487650392
www.brightwayhaul.com.au
brightwayhaulandupkeep@mailbox.example

On the back of the card I would like to list some of the types of service we offer (clean - move - repairs/maintenance) which are:
CLEAN - windows, gutters, solar panels, driveways/paths, carpets.
MOVE - Small/medium size house/office moves, large item pick-up & delivery, yard clean-up and removal.
General maintenance and repairs.

I would like the blue logo on a gray background.

Thanks

```html
<!DOCTYPE html>
<html lang="en">
<head>
<meta charset="utf-8">
<title>Brightway Haul &amp; Upkeep Services – Business Card</title>
<link rel="stylesheet" href="https://fonts.googleapis.com/css2?family=Jost:wght@400;500;600&display=swap">
<style>
  :root {
    --stage: #2c2c2e;
    --card-grey: #4b4e53;
    --card-grey-deep: #3f4246;
    --brand-blue: #2f7fc6;
    --brand-blue-light: #4fa0e0;
    --paper: #fbfbfb;
    --paper-shade: #eeeeee;
    --ink-grey: #8a8a8a;
    --ink-light: #d9dbde;
    --white: #ffffff;
  }
  * { box-sizing: border-box; margin: 0; padding: 0; }
  html, body {
    width: 1200px; height: 900px; overflow: hidden;
    background: var(--stage);
    font-family: "Jost", "Helvetica Neue", Arial, sans-serif;
  }
  .stage { position: relative; width: 1200px; height: 900px; }
  .card {
    position: absolute; left: 250px; width: 700px; height: 400px;
    border-radius: 3px; overflow: hidden;
    box-shadow: 0 14px 30px rgba(0,0,0,.5);
  }

  /* back side: blue name on grey */
  .card--back {
    top: 40px;
    background: linear-gradient(135deg, var(--card-grey) 0%, var(--card-grey-deep) 100%);
    color: var(--ink-light);
  }
  .brand { display: flex; align-items: center; gap: 12px; }
  .brand__dot { width: 14px; height: 14px; border-radius: 50%; background: currentColor; flex: none; }
  .brand__name { font-weight: 500; letter-spacing: .5px; text-transform: uppercase; white-space: nowrap; }

  .card--back .brand {
    position: absolute; left: 0; right: 0; top: 48px;
    justify-content: center; color: var(--brand-blue-light);
  }
  .card--back .brand__name { font-size: 28px; }

  .services {
    position: absolute; left: 60px; right: 60px; top: 120px;
    display: grid; grid-template-columns: 1fr 1fr 1fr; gap: 28px;
    list-style: none;
  }
  .service {
    border-top: 2px solid var(--brand-blue-light);
    padding-top: 12px;
  }
  .service__title {
    font-size: 17px; font-weight: 600; letter-spacing: 1.5px;
    color: var(--brand-blue-light); margin-bottom: 8px;
  }
  .service__text { font-size: 13.5px; line-height: 1.5; color: var(--ink-light); }

  .card--back .web {
    position: absolute; right: 60px; bottom: 40px;
    font-size: 16px; letter-spacing: 1px; color: var(--ink-light);
  }

  /* front side */
  .card--front {
    top: 470px;
    background: linear-gradient(160deg, var(--white) 0%, var(--paper) 55%, var(--paper-shade) 100%);
  }
  .card--front .brand {
    position: absolute; right: 50px; top: 52px; color: var(--brand-blue);
  }
  .card--front .brand__name { font-size: 22px; }
  .card--front .brand__dot { width: 12px; height: 12px; }
  .edge-marker { position: absolute; left: 0; top: 230px; width: 22px; height: 40px; }

  .contact { position: absolute; left: 50px; top: 228px; color: var(--ink-grey); }
  .contact__name {
    font-size: 22px; font-weight: 500; color: var(--brand-blue); margin-bottom: 14px;
  }
  .contact__divider { color: var(--brand-blue); margin: 0 6px; font-weight: 400; }
  .contact__role { font-weight: 400; }
  .contact__row {
    display: flex; align-items: flex-start; gap: 10px;
    font-size: 14px; line-height: 1.4; margin-bottom: 6px;
  }
  .contact__row svg { flex: none; margin-top: 2px; }
  .contact__inline { gap: 24px; }
  .contact__inline span { display: flex; align-items: center; gap: 8px; }
</style>
</head>
<body>
<main class="stage">

  <section class="card card--back" aria-label="Card back">
    <div class="brand">
      <span class="brand__dot"></span>
      <span class="brand__name">Brightway Haul &amp; Upkeep Services</span>
    </div>

    <ul class="services">
      <li class="service">
        <h3 class="service__title">CLEAN</h3>
        <p class="service__text">Windows, gutters, solar panels, driveways/paths, carpets.</p>
      </li>
      <li class="service">
        <h3 class="service__title">MOVE</h3>
        <p class="service__text">Small/medium house &amp; office moves, large item pick-up &amp; delivery, yard clean-up and removal.</p>
      </li>
      <li class="service">
        <h3 class="service__title">MAINTENANCE</h3>
        <p class="service__text">General maintenance and repairs.</p>
      </li>
    </ul>

    <p class="web">www.brightwayhaul.com.au</p>
  </section>

  <section class="card card--front" aria-label="Card front">
    <div class="brand">
      <span class="brand__dot"></span>
      <span class="brand__name">Brightway Haul &amp; Upkeep Services</span>
    </div>

    <svg class="edge-marker" viewBox="0 0 22 40" aria-hidden="true">
      <polygon points="0,0 22,20 0,40" fill="var(--brand-blue)"/>
    </svg>

    <div class="contact">
      <p class="contact__name">Sam Carter<span class="contact__divider">|</span><span class="contact__role">President</span></p>

      <div class="contact__row">
        <svg width="12" height="16" viewBox="0 0 12 16" aria-hidden="true">
          <path d="M6 0a6 6 0 0 0-6 6c0 4.5 6 10 6 10s6-5.5 6-10a6 6 0 0 0-6-6zm0 8.5A2.5 2.5 0 1 1 6 3.5a2.5 2.5 0 0 1 0 5z" fill="var(--brand-blue)"/>
        </svg>
        <span>Suit 12 Your Street 34 Your City<br>56 Country 78901</span>
      </div>

      <div class="contact__row contact__inline">
        <span>
          <svg width="14" height="14" viewBox="0 0 14 14" aria-hidden="true">
            <path d="M3 1l2 3-1.3 1.3a8 8 0 0 0 5 5L10 9l3 2-1 2.5C6 13.5.5 8 .5 2z" fill="var(--brand-blue)"/>
          </svg>
          0487 650 392
        </span>
        <span>
          <svg width="15" height="11" viewBox="0 0 15 11" aria-hidden="true">
            <rect x="0" y="0" width="15" height="11" rx="1" fill="var(--brand-blue)"/>
            <polyline points="1,1 7.5,6 14,1" fill="none" stroke="var(--white)" stroke-width="1.2"/>
          </svg>
          brightwayhaulandupkeep@mailbox.example
        </span>
      </div>

      <div class="contact__row">
        <svg width="15" height="13" viewBox="0 0 15 13" aria-hidden="true">
          <path d="M1 4c0-2 3-3 6.5-3S14 2 14 4v1h-3V3.5H4V5H1zM3 6h9l1.5 6h-12z" fill="var(--brand-blue)"/>
        </svg>
        <span>0487 650 392</span>
      </div>
    </div>
  </section>

</main>
</body>
</html>
```